Business Card Design for company

We want new business cards. We'd like something different-- yet still highly professional. Our tagline is Providing leadership, delivering success. Stock photos are ok, as long as they are relevant and look upscale.

Target Market(s)

Architecture/Business Management Consulting/Engineering Consulting

Contact Information for Business Card

dark gray background with pops of blue might be good, but you tell me. You're the designers. Rounded corners might be nice, but again, you tell me.

Font styles to use
Serif
Sans Serif

Colors
3276b5
5c5c5c
9d9d9d
fbfbfb

Requirements
Nice to have
• Something different, but still very professional.

```html
<!DOCTYPE html>
<html lang="en">
<head>
<meta charset="utf-8">
<title>Norvale Partners – Business Card</title>
<link href="https://fonts.googleapis.com/css2?family=Montserrat:wght@400;500;600;700&display=swap" rel="stylesheet">
<style>
  :root {
    --stage: #2b2b2b;
    --card: #4b4b4c;
    --card-deep: #444445;
    --map-light: #5c5c5c;
    --blue: #3276b5;
    --light: #fbfbfb;
    --muted: #9d9d9d;
    --ink: #5c5c5c;
  }
  * { margin: 0; padding: 0; box-sizing: border-box; }
  html, body { width: 1200px; height: 900px; overflow: hidden; }
  body {
    background: var(--stage);
    font-family: "Montserrat", sans-serif;
    color: var(--light);
    display: flex;
    flex-direction: column;
    align-items: center;
    justify-content: center;
    gap: 40px;
  }
  .card {
    position: relative;
    width: 630px;
    height: 360px;
    background: var(--card);
    overflow: hidden;
    box-shadow: 0 10px 30px rgba(0,0,0,.45);
  }
  .world-map {
    position: absolute;
    inset: 0;
    background: radial-gradient(ellipse at 45% 40%, var(--map-light) 0%, var(--card-deep) 75%);
    opacity: .8;
  }
  /* Front */
  .front-brand {
    position: absolute;
    left: 0; right: 0; top: 92px;
    text-align: center;
  }
  .brand-name {
    font-weight: 600;
    font-size: 66px;
    letter-spacing: 2px;
    line-height: 1;
    color: var(--light);
  }
  .brand-sub {
    font-weight: 600;
    font-size: 24px;
    letter-spacing: 4px;
    margin-top: 12px;
    color: var(--light);
  }
  .tagline {
    position: absolute;
    left: 0; right: 0; bottom: 60px;
    text-align: center;
    font-size: 11px;
    letter-spacing: 2.4px;
    color: var(--light);
  }
  /* Back */
  .back-brand {
    position: absolute;
    left: 40px; top: 110px;
    width: 280px;
    text-align: center;
  }
  .back-brand .brand-name { font-size: 48px; color: var(--light); }
  .back-brand .brand-sub { font-size: 18px; letter-spacing: 3px; margin-top: 10px; }
  .divider {
    position: absolute;
    left: 338px; top: 70px;
    width: 1px; height: 160px;
    background: var(--muted);
  }
  .contact {
    position: absolute;
    left: 362px; top: 62px;
  }
  .person-name {
    font-weight: 700;
    font-size: 18px;
    letter-spacing: 1.5px;
  }
  .person-role {
    font-size: 11px;
    margin: 3px 0 12px;
  }
  .contact-list { list-style: none; }
  .contact-list li {
    display: flex;
    align-items: center;
    gap: 8px;
    font-size: 11.5px;
    line-height: 20px;
    color: var(--light);
  }
  .contact-list svg { width: 10px; height: 10px; fill: none; stroke: var(--light); stroke-width: 1.4; }
  .address-rule {
    position: absolute;
    left: 0; right: 0; bottom: 76px;
    height: 2px;
    background: var(--muted);
  }
  .address-band {
    position: absolute;
    left: 0; right: 0; bottom: 0;
    height: 66px;
    background: var(--light);
    color: var(--ink);
    font-size: 13px;
    display: flex;
    align-items: center;
    justify-content: center;
  }
</style>
</head>
<body>

  <section class="card card-front">
    <div class="world-map" role="img" aria-label="Faint world map in grey tones"></div>
    <div class="front-brand">
      <div class="brand-name">NORVALE</div>
      <div class="brand-sub">PARTNERS</div>
    </div>
    <p class="tagline">PROVIDING LEADERSHIP | DELIVERING SUCCESS</p>
  </section>

  <section class="card card-back">
    <div class="world-map" role="img" aria-label="Dotted world map in grey tones"></div>
    <div class="back-brand">
      <div class="brand-name">NORVALE</div>
      <div class="brand-sub">PARTNERS</div>
    </div>
    <div class="divider"></div>
    <div class="contact">
      <div class="person-name">DANIEL ASHBY</div>
      <div class="person-role">Design Consultant</div>
      <ul class="contact-list">
        <li><svg viewBox="0 0 10 10"><rect x="2.5" y="0.8" width="5" height="8.4" rx="1"/></svg>555-010-4821</li>
        <li><svg viewBox="0 0 10 10"><path d="M2 1 L4 1 L4.5 3 L3.3 4 Q4.5 6 6 6.7 L7 5.5 L9 6 L9 8 Q5 9 1 3 Z"/></svg>01632 960418 (Eastford)</li>
        <li><svg viewBox="0 0 10 10"><path d="M2 1 L4 1 L4.5 3 L3.3 4 Q4.5 6 6 6.7 L7 5.5 L9 6 L9 8 Q5 9 1 3 Z"/></svg>01632 960725 (Millbrook)</li>
        <li><svg viewBox="0 0 10 10"><rect x="0.8" y="2" width="8.4" height="6"/><path d="M0.8 2 L5 5.5 L9.2 2"/></svg>info@norvalepartners</li>
        <li><svg viewBox="0 0 10 10"><circle cx="5" cy="5" r="4.2"/><path d="M0.8 5 H9.2 M5 0.8 Q2.5 5 5 9.2 M5 0.8 Q7.5 5 5 9.2"/></svg>www.norvalepartners.com</li>
      </ul>
    </div>
    <div class="address-rule"></div>
    <div class="address-band">Unit 8, The Hollin Centre, Brook Yard, Eastford, Kent EF2 4QT</div>
  </section>

</body>
</html>
```